SaaS Early tech startup business card design

Unique design for experience ecommerce platform company. the business cards will be used by executive members. conformance with color code is required.

```html
<!DOCTYPE html>
<html lang="en">
<head>
<meta charset="utf-8">
<title>kovo business cards</title>
<link href="https://fonts.googleapis.com/css2?family=Roboto:wght@400;500;700;900&display=swap" rel="stylesheet">
<style>
  :root {
    --bg: #1f1f20;
    --teal: #16a899;
    --teal-light: #1fbfa6;
    --ocean: #0b6fa0;
    --navy-text: #0a5d8c;
    --charcoal: #2b2729;
    --paper: #f7f7f6;
    --ink: #4a4a4a;
    --white: #ffffff;
  }
  * { box-sizing: border-box; margin: 0; padding: 0; }
  html, body { width: 1200px; height: 874px; overflow: hidden; background: var(--bg); }
  body { position: relative; font-family: "Roboto", sans-serif; }

  .card {
    position: absolute;
    left: 320px;
    width: 560px;
    height: 320px;
    border-radius: 24px;
    overflow: hidden;
  }
  .card--front { top: 88px; }
  .card--back { top: 466px; display: flex; }

  .front-field {
    position: absolute; inset: 0;
    background: linear-gradient(160deg, var(--teal) 0%, #128f9d 50%, var(--ocean) 100%);
  }
  .front-logo {
    position: absolute;
    right: 48px; bottom: 44px;
    font-weight: 900;
    font-size: 78px;
    letter-spacing: -1px;
    line-height: 1;
    color: var(--white);
  }

  .back-brand {
    width: 300px;
    background: var(--charcoal);
    display: flex; align-items: center; justify-content: center;
  }
  .back-logo {
    font-weight: 900;
    font-size: 74px;
    letter-spacing: -1px;
    line-height: 1;
    color: var(--teal-light);
  }
  .accent-band {
    width: 12px;
    background: linear-gradient(180deg, var(--ocean) 0%, var(--teal) 55%, var(--teal-light) 100%);
  }
  .back-details {
    flex: 1;
    background: var(--paper);
    padding: 62px 0 0 30px;
  }
  .person-name {
    font-weight: 700;
    font-size: 21px;
    color: var(--navy-text);
    letter-spacing: 0.3px;
  }
  .person-title {
    font-weight: 500;
    font-size: 14px;
    color: var(--teal);
    margin-bottom: 12px;
  }
  .address {
    font-size: 13.5px;
    color: var(--ink);
    line-height: 1.3;
    margin-bottom: 10px;
  }
  .contact-list { list-style: none; }
  .contact-item {
    display: flex; align-items: center; gap: 9px;
    font-size: 13.5px; line-height: 1.45;
    color: var(--ink);
  }
  .contact-icon { width: 12px; height: 12px; fill: var(--teal); flex: none; }
</style>
</head>
<body>

<section class="card card--front">
  <div class="front-field" role="img" aria-label="Teal to ocean-blue checkered square pattern background"></div>
  <div class="front-logo">kovo</div>
</section>

<section class="card card--back">
  <div class="back-brand">
    <div class="back-logo">kovo</div>
  </div>
  <div class="accent-band" role="img" aria-label="Vertical band of small blue and teal pixel squares"></div>
  <div class="back-details">
    <p class="person-name">DANIEL REYES</p>
    <p class="person-title">President</p>
    <p class="address">4120 Birchwood Drive<br>Juneau, Alaska 99801</p>
    <ul class="contact-list">
      <li class="contact-item">
        <svg class="contact-icon" viewBox="0 0 24 24"><path d="M6.6 10.8a15 15 0 0 0 6.6 6.6l2.2-2.2a1 1 0 0 1 1-.25 11.4 11.4 0 0 0 3.6.57 1 1 0 0 1 1 1V20a1 1 0 0 1-1 1A17 17 0 0 1 3 4a1 1 0 0 1 1-1h3.5a1 1 0 0 1 1 1c0 1.25.2 2.45.57 3.57a1 1 0 0 1-.25 1z"/></svg>
        555-214-7730
      </li>
      <li class="contact-item">
        <svg class="contact-icon" viewBox="0 0 24 24"><path d="M7 1h10a2 2 0 0 1 2 2v18a2 2 0 0 1-2 2H7a2 2 0 0 1-2-2V3a2 2 0 0 1 2-2zm0 3v15h10V4z"/></svg>
        555-318-4462
      </li>
      <li class="contact-item">
        <svg class="contact-icon" viewBox="0 0 24 24"><path d="M6 2h12v5H6zM3 8h18a2 2 0 0 1 2 2v7h-4v5H5v-5H1v-7a2 2 0 0 1 2-2zm4 8v4h10v-4z"/></svg>
        555-402-1189
      </li>
      <li class="contact-item">
        <svg class="contact-icon" viewBox="0 0 24 24"><path d="M2 4h20v16H2zm2 2v.5l8 5 8-5V6zm0 3v9h16V9l-8 5z"/></svg>
        hello@kovo.com
      </li>
      <li class="contact-item">
        <svg class="contact-icon" viewBox="0 0 24 24"><circle cx="12" cy="12" r="11"/></svg>
        www.kovo.com
      </li>
    </ul>
  </div>
</section>

</body>
</html>
```